ULMIRA card Technical Architecture

Hello everyone ULMIRA: It is a consulting firm in Architecture and Construction. I require a card duplexing, sober, elegant, classic but not boring. Update 1: Use the following data for the card. Name: Gonzalo Pereda Mauricio Villalta Position: COO Twitter: @ulmiraAT Homepage: ulmira-example.com home address not include the participation of all thank you.

Target Market(s)

Construction companies, Architects and Consulting Engineers

Industry/Entity Type

Consulting

Contact Information for Business Card

Los campos que debe tener:
Nombre, Cargo, email, homepage y twitter

Font styles to use
Serif
Sans Serif
Other font styles liked:
• Me gustan playfair display, open sans y roboto, pero estoy sujeto a sus propuestas

Requirements
Must have
• Colors: Present combined proposals in white, red, gray and black Update 1: The two names must be clearly differentiated from the two surnames
Nice to have
• They are free to present their best proposals. I will bring them immediate feedback to the extent you can go see their designs. Complete data for card and logo files will give the winner the

```html
<!DOCTYPE html>
<html lang="es">
<head>
<meta charset="utf-8">
<title>ULMIRA – Business Card</title>
<link href="https://fonts.googleapis.com/css2?family=Open+Sans:wght@400;600;700&family=Raleway:wght@300;400&display=swap" rel="stylesheet">
<style>
  :root {
    --backdrop: #3a332f;
    --card: #2b2b2b;
    --card-edge: #1e1e1e;
    --red: #d11a22;
    --red-dark: #8e0d12;
    --white: #ffffff;
    --grey-light: #d9d9d9;
  }
  * { box-sizing: border-box; margin: 0; padding: 0; }
  html, body {
    width: 1200px;
    height: 844px;
    overflow: hidden;
    background: var(--backdrop);
  }
  .canvas {
    position: relative;
    width: 1200px;
    height: 844px;
  }
  .card {
    position: absolute;
    top: 267px;
    width: 540px;
    height: 310px;
    background: var(--card);
    box-shadow: 0 8px 24px rgba(0,0,0,.45);
    overflow: hidden;
  }
  .card--back { left: 40px; }
  .card--front { left: 620px; }

  /* back side */
  .band {
    position: absolute;
    left: 0;
    width: 100%;
    height: 14px;
    background: linear-gradient(to bottom, #f0333a, var(--red) 45%, var(--red-dark));
  }
  .band--top { top: 0; }
  .band--bottom { bottom: 0; }
  .contact {
    position: absolute;
    left: 200px;
    top: 96px;
    color: var(--white);
    font-family: "Open Sans", sans-serif;
  }
  .contact__name {
    font-size: 19px;
    font-weight: 700;
    line-height: 1.1;
  }
  .contact__role {
    font-size: 12px;
    font-weight: 400;
    color: var(--grey-light);
    margin-left: 18px;
    margin-bottom: 28px;
  }
  .contact__list {
    list-style: none;
    font-size: 13px;
    line-height: 1.5;
    margin-left: 46px;
  }

  /* front side */
  .tab {
    position: absolute;
    width: 26px;
    height: 32px;
    background: linear-gradient(to bottom, #f0333a, var(--red) 50%, var(--red-dark));
    border-right: 4px solid var(--grey-light);
  }
  .tab--right { right: 0; top: 16px; }
  .tab--left { left: 0; top: 128px; }
  .brand {
    position: absolute;
    left: 214px;
    top: 108px;
    font-family: "Raleway", sans-serif;
    color: var(--white);
    text-align: center;
  }
  .brand__name {
    font-size: 44px;
    font-weight: 300;
    letter-spacing: 14px;
    padding-bottom: 6px;
    border-bottom: 1px solid var(--grey-light);
  }
  .brand__tagline {
    margin-top: 6px;
    font-size: 13px;
    font-weight: 400;
    letter-spacing: 5px;
    color: var(--grey-light);
  }
</style>
</head>
<body>
<main class="canvas">
  <section class="card card--back" aria-label="Card back">
    <div class="band band--top"></div>
    <div class="contact">
      <p class="contact__name">Tomas Rivera</p>
      <p class="contact__role">Managing Director</p>
      <ul class="contact__list">
        <li>C: (055)-300-0199</li>
        <li>E: hola@ulmira-example.com</li>
        <li>W: www.ulmira-example.com</li>
        <li>T: @ulmiraAT</li>
      </ul>
    </div>
    <div class="band band--bottom"></div>
  </section>

  <section class="card card--front" aria-label="Card front">
    <div class="tab tab--right"></div>
    <div class="tab tab--left"></div>
    <div class="brand">
      <p class="brand__name">ULMIRA</p>
      <p class="brand__tagline">ARQUITECTURA TÉCNICA</p>
    </div>
  </section>
</main>
</body>
</html>
```